Want to fly? Flight school needs a roll up

Hello designers

We are a small aviation club with around 100 members. We love flying and therefore offer free flight lessons for young people at our glider flight school.
The young people only have to pay a flat rate of €300 for the aircraft until their first solo flight.
To advertise the flight school we now need a roll up banner measuring 85cm x 200cm. You can find the data sheet for the banner in the appendix.
Content of the roll up banner:
Advertising for our flight school so that we can attract new members
The banner should be designed in our club colors blue/white
The banner is aimed at all people who want to get a glider license
A great offer for young people up to the age of 25 should be placed on the banner with a reference to the text “Offer only applies to people up to the age of 25. Included in the flat rate of €300 is training on the glider up to the first "solo flight"
The banner is intended to advertise training with a glider. Therefore the wish would be for a glider to be depicted

Here is a link to our current homepage

https://www.lgk-tarnholm.de/

https://www.vidoplex.example/watch?v=Qk7pL2xNz9c

Target Market(s)

Young people from 14 years to 30 years

Colors
0054AA
0677BA
7BADD7
CADEEF
E8F1F8

Requirements
Nice to have
• Glider / club logo
Should not have
• Too much text

```html
<!DOCTYPE html>
<html lang="en">
<head>
<meta charset="utf-8">
<title>Free Flight Lessons – Roll Up</title>
<link rel="stylesheet" href="https://fonts.googleapis.com/css2?family=Poppins:wght@400;500;600;700;800;900&display=swap">
<style>
  :root {
    --navy: #0a14a0;
    --navy-deep: #000b86;
    --ring-blue: #1a28b4;
    --gold: #e8a93a;
    --red: #b50d14;
    --white: #ffffff;
    --ink: #0b0b0b;
    --sky-top: #9fd2ef;
    --sky-mid: #c7dfec;
    --city: #7d8fa6;
  }
  * { margin: 0; padding: 0; box-sizing: border-box; }
  html, body { width: 1200px; height: 2835px; overflow: hidden; background: var(--white); }
  body { font-family: "Poppins", sans-serif; }
  .rollup { position: relative; width: 1200px; height: 2835px; overflow: hidden; background: var(--white); }

  .hero-photo {
    position: absolute; left: 0; top: 0; width: 1200px; height: 722px;
    background: linear-gradient(180deg, var(--sky-top) 0%, var(--sky-mid) 50%, #a9bccb 72%, var(--city) 100%);
  }
  .hero-rule { position: absolute; left: 0; top: 716px; width: 1200px; height: 8px; background: #5b6e9a; }
  .hero-rings { position: absolute; left: 0; top: 0; }

  .blue-band {
    position: absolute; left: 0; top: 722px; width: 1200px; height: 984px;
    background: linear-gradient(180deg, var(--navy) 0%, var(--navy) 60%, var(--navy-deep) 100%);
  }

  .club-badge {
    position: absolute; left: 434px; top: 557px; width: 330px; height: 330px;
    border-radius: 50%; background: var(--white); border: 8px solid var(--navy);
    display: flex; align-items: center; justify-content: center; text-align: center;
  }
  .club-badge__name { color: var(--navy); font-weight: 700; font-size: 30px; line-height: 1.2; }

  .tagline {
    position: absolute; left: 122px; top: 938px; width: 956px; height: 81px;
    background: var(--red); display: flex; align-items: center; justify-content: center;
    font-weight: 800; font-size: 58px; line-height: 1; letter-spacing: 7px; color: var(--white);
  }
  .tagline__accent { color: var(--gold); margin-left: 18px; }

  .headline-free {
    position: absolute; left: 0; top: 991px; width: 1200px; text-align: center;
    font-weight: 800; font-size: 362px; line-height: 1; color: var(--gold); letter-spacing: -8px;
  }
  .headline-lessons {
    position: absolute; left: 0; top: 1318px; width: 1200px; text-align: center;
    font-weight: 800; font-size: 128px; line-height: 1; color: var(--white); letter-spacing: -1px;
  }
  .headline-sub {
    position: absolute; left: 0; top: 1452px; width: 1200px; text-align: center;
    font-weight: 600; font-size: 47px; line-height: 1.2; color: var(--white);
  }

  .discipline-photo {
    position: absolute; border-radius: 50%; border: 9px solid var(--gold);
    box-shadow: 0 8px 18px rgba(0,0,0,.25);
  }
  .discipline-photo--gliding { left: 86px; top: 1636px; width: 350px; height: 350px;
    background: radial-gradient(circle at 40% 40%, #e9eef2, #9eb0b0 60%, #6f7d5a); }
  .discipline-photo--motor { left: 397px; top: 1590px; width: 404px; height: 404px; z-index: 2;
    background: linear-gradient(180deg, #8c9a52 0%, #6f8a3a 55%, #8f8e78 100%); }
  .discipline-photo--powered { left: 762px; top: 1636px; width: 350px; height: 350px;
    background: linear-gradient(180deg, #d4e3ea 0%, #b7c8cf 55%, #3e5a2c 70%, #5d7f3a 100%); }

  .discipline-label {
    position: absolute; width: 320px; text-align: center;
    font-weight: 700; font-size: 46px; line-height: 51px; color: var(--ink);
  }
  .discipline-label--gliding { left: 94px; top: 2040px; }
  .discipline-label--motor { left: 439px; top: 2030px; }
  .discipline-label--powered { left: 770px; top: 2030px; }

  .price { position: absolute; left: 92px; top: 2178px; }
  .price__amount { font-weight: 800; font-size: 150px; line-height: 1; color: var(--navy); letter-spacing: -4px; }
  .price__currency { font-size: 80px; vertical-align: 52px; letter-spacing: 0; }
  .price__note { font-weight: 600; font-size: 38px; line-height: 41px; color: var(--ink); margin-top: -18px; }
  .price__solo { font-weight: 800; font-size: 64px; line-height: 1; color: var(--navy); letter-spacing: -1px; margin-top: 4px; }

  .age-offer { position: absolute; left: 550px; top: 2215px; width: 565px; height: 210px; display: flex; }
  .age-offer__text {
    width: 385px; background: var(--red); color: var(--white); white-space: nowrap;
    font-weight: 400; font-size: 37px; line-height: 49px; padding: 32px 0 0 18px;
  }
  .age-offer__age {
    flex: 1; background: var(--navy); color: var(--white);
    display: flex; align-items: center; justify-content: center;
    font-weight: 700; font-size: 124px; line-height: 1; letter-spacing: -4px;
  }
  .train-note {
    position: absolute; left: 545px; top: 2418px; width: 575px; text-align: center;
    font-weight: 700; font-size: 40px; line-height: 1; letter-spacing: 7px; color: var(--navy); white-space: nowrap;
  }

  .cta-title {
    position: absolute; left: 0; top: 2523px; width: 1200px; text-align: center;
    font-weight: 800; font-size: 122px; line-height: 1; color: var(--ink); letter-spacing: -2px;
  }
  .cta-url {
    position: absolute; left: 85px; top: 2660px; width: 1031px; height: 94px;
    background: var(--red); color: var(--white); border-radius: 3px;
    box-shadow: 0 8px 10px rgba(0,0,0,.3);
    display: flex; align-items: center; justify-content: center;
    font-size: 60px; line-height: 1; letter-spacing: 5px; font-weight: 400;
  }
  .cta-url strong { font-weight: 800; }
</style>
</head>
<body>
<main class="rollup">
  <div class="hero-photo" role="img" aria-label="Red and white aerobatic plane flying over a hazy city skyline"></div>
  <div class="hero-rule"></div>
  <svg class="hero-rings" width="1200" height="722" viewBox="0 0 1200 722" aria-hidden="true">
    <g fill="none" stroke="var(--ring-blue)" stroke-linecap="round">
      <path d="M 355 170 A 420 420 0 0 1 890 150" stroke-width="12"/>
      <path d="M 395 185 A 380 380 0 0 1 860 200" stroke-width="9"/>
      <path d="M 235 320 A 420 420 0 0 0 290 715" stroke-width="12"/>
      <path d="M 270 330 A 380 380 0 0 0 320 715" stroke-width="9"/>
      <path d="M 1003 360 A 420 420 0 0 1 950 715" stroke-width="12"/>
      <path d="M 970 370 A 380 380 0 0 1 925 715" stroke-width="9"/>
    </g>
  </svg>

  <div class="blue-band"></div>

  <div class="club-badge">
    <span class="club-badge__name">Luftsportklub<br>Tarnholm e.V.</span>
  </div>

  <div class="tagline">BECOME A <span class="tagline__accent">PILOT NOW!</span></div>
  <h1 class="headline-free">FREE</h1>
  <h2 class="headline-lessons">FLIGHT LESSONS</h2>
  <p class="headline-sub">For young people at our glider flight school</p>

  <div class="discipline-photo discipline-photo--gliding" role="img" aria-label="Glider cockpit canopy close-up"></div>
  <div class="discipline-photo discipline-photo--powered" role="img" aria-label="Light powered aircraft landing over trees"></div>
  <div class="discipline-photo discipline-photo--motor" role="img" aria-label="Motor glider taking off from a grass airfield"></div>

  <div class="discipline-label discipline-label--gliding">GLIDING</div>
  <div class="discipline-label discipline-label--motor">MOTOR<br>GLIDER</div>
  <div class="discipline-label discipline-label--powered">POWERED<br>FLIGHT</div>

  <div class="price">
    <div class="price__amount"><span class="price__currency">€</span>300</div>
    <div class="price__note">FOR THE AIRCRAFT<br>UNTIL THEIR FIRST</div>
    <div class="price__solo">SOLO FLIGHT</div>
  </div>

  <div class="age-offer">
    <div class="age-offer__text">Offer only<br>applies to people<br>up to the age of</div>
    <div class="age-offer__age">25</div>
  </div>
  <div class="train-note">TRAIN WITH A GLIDER</div>

  <div class="cta-title">BOOK ONLINE</div>
  <div class="cta-url">www.<strong>lgk-tarnholm</strong>.de</div>
</main>
</body>
</html>
```